brightwell - Property Management DL Card

I am after a savvy designer to cut through junk mail! so many real estate agents use flyers to promote themselves and their business and usually sales. We are a property management firm (residential) and we want to represent landlords that have existing investment properties and need a quality agent to represent them. Can you help?
DL size, will be printed and delivered to mailboxes. For a look at our website go to www.brightwellrs.com.au. Keep it simple and clutter free.
it is to be double sided - with one side to be simple and clear - just our website, logo and telephone number on the back.
attached is our logo and our telephone number is 1300 48 92 16
the above are 2 essential elements to be included + our email address: admin@brightwellrs.com.au
also attached are our transparent price list

Target Market(s)
property investors,
people that manage properties themselves
Industry/Entity Type
Property Management
- arial
Look and feel

```html
<!DOCTYPE html>
<html lang="en">
<head>
<meta charset="utf-8">
<title>brightwell – Property Management DL Card</title>
<link rel="stylesheet" href="https://fonts.googleapis.com/css2?family=Open+Sans:wght@300;400;600&display=swap">
<style>
  :root {
    --page-bg: #d4d4d4;
    --card-black: #000000;
    --panel-black: #0a0a0a;
    --sand: #e2d7b4;
    --brick: #c4402a;
    --brick-text: #f0c2b4;
    --white: #ffffff;
    --soft-white: #e9e9e9;
    --phone-red: #d6402c;
    --rule-grey: #9a9a9a;
  }
  * { margin: 0; padding: 0; box-sizing: border-box; }
  html, body {
    width: 1200px; height: 1200px; overflow: hidden;
    background: var(--page-bg);
    font-family: "Open Sans", Arial, sans-serif;
  }
  .card { position: absolute; left: 120px; width: 998px; }

  /* Front side */
  .card--front { top: 58px; height: 498px; }
  .front__band-top { position: absolute; left: 0; top: 0; width: 100%; height: 65px; background: var(--sand); }
  .front__photo {
    position: absolute; left: 0; top: 65px; width: 716px; height: 360px;
    background:
      linear-gradient(180deg, rgba(230,225,210,0.55) 0%, rgba(0,0,0,0) 35%),
      linear-gradient(90deg, #3b352d 0%, #8d8474 22%, #6f6657 45%, #2a2521 62%, #a59d8c 80%, #3a342e 100%);
  }
  .front__photo::after {
    content: ""; position: absolute; left: 0; bottom: 0; width: 100%; height: 32%;
    background: linear-gradient(180deg, rgba(70,45,30,0) 0%, #4a3223 100%);
  }
  .front__brand-panel {
    position: absolute; left: 716px; top: 65px; width: 282px; height: 360px;
    background: var(--panel-black);
    display: flex; align-items: center; justify-content: center;
  }
  .brand-name {
    font-weight: 300; color: var(--white); letter-spacing: 0.5px; line-height: 1;
  }
  .front__brand-panel .brand-name { font-size: 40px; }

  .front__band-bottom {
    position: absolute; left: 0; top: 425px; width: 100%; height: 73px;
    background: var(--brick);
  }
  .band__headline {
    position: absolute; left: 52px; top: 23px;
    font-size: 20px; font-weight: 600; color: var(--brick-text);
  }
  .band__divider {
    position: absolute; left: 422px; top: 17px; width: 2px; height: 38px;
    background: var(--brick-text); opacity: 0.8;
  }
  .band__points {
    position: absolute; top: 15px; list-style: none;
    font-size: 16px; color: var(--white); line-height: 21px;
  }
  .band__points li::before { content: "•"; margin-right: 7px; }
  .band__points--a { left: 446px; }
  .band__points--b { left: 711px; }

  /* Back side */
  .card--back { top: 637px; height: 500px; background: var(--card-black); }
  .card--back .brand-name { position: absolute; left: 53px; top: 52px; font-size: 42px; }
  .contact {
    position: absolute; left: 557px; top: 381px;
    border-left: 2px solid var(--rule-grey);
    padding-left: 20px; font-size: 17.5px; line-height: 24px;
    color: var(--soft-white); letter-spacing: 0.4px;
  }
  .contact__phone { color: var(--phone-red); }
</style>
</head>
<body>
  <section class="card card--front">
    <div class="front__band-top"></div>
    <div class="front__photo" role="img" aria-label="Photo of a modern kitchen with dark cabinetry, stainless steel appliances and timber floor"></div>
    <div class="front__brand-panel">
      <span class="brand-name">brightwell</span>
    </div>
    <div class="front__band-bottom">
      <p class="band__headline">Property Management specialists</p>
      <span class="band__divider"></span>
      <ul class="band__points band__points--a">
        <li>Excellent communication</li>
        <li>Minimal vacancy</li>
      </ul>
      <ul class="band__points band__points--b">
        <li>No hidden extras</li>
        <li>The best rent return</li>
      </ul>
    </div>
  </section>

  <section class="card card--back">
    <span class="brand-name">brightwell</span>
    <address class="contact" style="font-style: normal;">
      <div class="contact__phone">1300 48 92 16</div>
      <div>PO Box B527, Harbourside NSW, 2150</div>
      <div>admin@brightwellrs.com.au</div>
    </address>
  </section>
</body>
</html>
```